Redesign to improve branding visibility and product messaging

Update the logo using the new logo provided attached.
Then, improve product messaging on the packaging, however leaving the colours, general blurbs, and the fruit/nut image outlines as they are (but open to make it simpler).
Please review photos Stockist 1" to 5" and recommend the new style for:
1 Energy Ball Bag
1 Energy Ball Inner Box
1 Cereal Bag
Key features:
1. Allow more transparent window to show more of the product inside.
2. Strong brand presence and clear nutritional call outs - keep in mind we display our products on supermarket shelves.
3. Product Messaging:
- 1st priority: Product Name
- 2nd priority: Nutritional call outs (All natural, GF, Vegan, High Fibre, No added sugar, etc.). This info is available in the current packaging and more info on the website.
- 3rd priority: Ingredients on front cover (example: 7 ingredients only: x1, x2, x3, x4, x5, x6, x7.)
- 4th priority: Locally Made by a nutritionist.
- 5th priority: Sugar content in the nutritional panel to say: From Healthy Natural Sources
Tips:
1. Use Style 1 as benchmark.
2. Use the other image references as follows:
Style 2 and 5 = Try do something similar for the energy ball bags.
Style 4 = Maybe add the line up of other flavours on the back or the side of the packaging for the energy ball box and the cereal bags.
Style 7 = Do something similar with regards to the use of real imagery on the packaging as if you can pick out the product right of the packaging. Note also how they list the ingredients on the front of packaging.
Style 8 = Do something similar - be proud about the real ingredients used.
Style 9 = An example of how much transparent area we can do, please suggest a nice unique transparent shape.
Style 10 = copy the way it communicates the health benefits very clearly.

```html
<!DOCTYPE html>
<html lang="en">
<head>
<meta charset="utf-8">
<title>Apricot &amp; Coconut Energy Ball – Bag Dieline</title>
<link href="https://fonts.googleapis.com/css2?family=Anton&family=Dancing+Script:wght@700&family=Montserrat:wght@600;700&family=Nunito:wght@700;900&family=Roboto:wght@400;500;700;900&display=swap" rel="stylesheet">
<style>
:root{
  --pink:#eea4c2;
  --magenta:#b24d89;
  --guide:#ee1fe3;
  --apricot:#fb7a5a;
  --window:#9aa9aa;
  --white:#ffffff;
  --ink:#1a1a1a;
  --badge-green:#2e8b3a;
}
*{margin:0;padding:0;box-sizing:border-box}
html,body{width:797px;height:1200px;overflow:hidden;background:var(--white)}
.sheet{position:relative;width:797px;height:1200px;font-family:"Roboto",sans-serif;color:var(--white)}
.abs{position:absolute}

/* panels */
.panel-top{left:126px;top:30px;width:648px;height:263px;background:var(--pink);overflow:hidden}
.panel-window{left:126px;top:293px;width:648px;height:317px;
  background:radial-gradient(ellipse 55% 75% at 50% 55%,#b49d7a 0%,#a9a48f 45%,var(--window) 80%);overflow:hidden}
.panel-front{left:126px;top:610px;width:648px;height:145px;background:var(--pink);overflow:hidden}
.panel-back{left:126px;top:755px;width:648px;height:264px;background:var(--pink);overflow:hidden}

.flipped{position:absolute;inset:0;transform:rotate(180deg)}

/* decorations */
.deco{position:absolute}
.deco-apricot{background:var(--apricot);border-radius:50%}
.deco-coconut{background:var(--white);border-radius:50%}
.deco-nut{border:2px solid var(--white);border-radius:50% 50% 45% 45%;opacity:.8}

/* top panel copy (reads upside down) */
.benefit-head{position:absolute;left:0;width:648px;top:24px;text-align:center;font-family:"Montserrat",sans-serif;font-weight:700;font-size:16px;letter-spacing:.3px}
.benefit-copy{position:absolute;left:79px;width:490px;top:56px;text-align:center;font-size:11.5px;line-height:16px}
.join{position:absolute;left:0;width:648px;top:131px;text-align:center;font-family:"Montserrat",sans-serif;font-weight:600;font-size:11.5px}
.rule{position:absolute;left:150px;width:350px;top:156px;height:1px;background:rgba(255,255,255,.7)}
.url{position:absolute;left:0;width:648px;top:162px;text-align:center;font-family:"Montserrat",sans-serif;font-weight:700;font-size:21px;letter-spacing:.3px}
.url::before,.social span::before{content:"";display:inline-block;width:.8em;height:.8em;border-radius:50%;background:var(--white);margin-right:6px;vertical-align:-1px}
.social{position:absolute;left:0;width:648px;top:194px;text-align:center;font-family:"Montserrat",sans-serif;font-weight:600;font-size:15px}
.social span{margin:0 8px}

/* window */
.title{position:absolute;left:164px;font-family:"Anton",sans-serif;font-size:80px;line-height:80px;letter-spacing:-.5px;white-space:nowrap}
.title-1{top:342px;color:var(--white)}
.title-2{top:419px;color:var(--white)}
.title-3{top:496px;color:var(--pink)}
.ampersand{position:absolute;left:394px;top:372px;font-family:"Dancing Script",cursive;font-size:46px;color:var(--white)}
.made-local{position:absolute;left:425px;top:418px;width:100px;text-align:center;font-family:"Montserrat",sans-serif;font-weight:700;font-size:10px;line-height:13px;letter-spacing:1.5px}
.stamp-caption{position:absolute;left:420px;top:492px;width:110px;text-align:center;font-family:"Montserrat",sans-serif;font-weight:700;font-size:8px}

.brand-banner{position:absolute;left:551px;top:294px;width:157px;height:188px;background:var(--magenta);
  clip-path:polygon(0 0,100% 0,100% 100%,95% 97%,90% 100%,85% 97%,80% 100%,75% 97%,70% 100%,65% 97%,60% 100%,55% 97%,50% 100%,45% 97%,40% 100%,35% 97%,30% 100%,25% 97%,20% 100%,15% 97%,10% 100%,5% 97%,0 100%)}
.brand-name{position:absolute;left:0;right:0;top:112px;text-align:center;font-family:"Montserrat",sans-serif;font-weight:700;font-size:17px;line-height:20px}

.ing-count{position:absolute;left:542px;top:524px;width:82px;transform:rotate(-90deg);text-align:center;font-family:"Anton",sans-serif;font-size:15px;color:var(--white)}
.ing-list{position:absolute;left:594px;top:494px;font-family:"Nunito",sans-serif;font-weight:900;font-size:11.5px;line-height:14.5px;list-style:none}

/* front lower */
.claims{position:absolute;left:280px;top:624px;display:flex;font-size:13.5px}
.claim{display:flex;flex-direction:column;align-items:center}
.claim svg{width:31px;height:31px;margin-bottom:5px}
.claim-sep{margin:36px 10px 0}
.benefit-pill{position:absolute;left:175px;top:689px;width:530px;height:25px;border-radius:12.5px;background:var(--magenta);font-size:12.2px;line-height:25px;text-align:center;white-space:nowrap}
.net{position:absolute;width:648px;top:723px;left:126px;text-align:center;font-family:"Montserrat",sans-serif;font-weight:700;font-size:14.5px;letter-spacing:3px}

/* back (reads upside down) */
.nip{position:absolute;left:44px;top:49px;width:193px;height:194px;background:var(--magenta);font-size:6.6px;line-height:1.15}
.nip-head{padding:4px 6px 3px;border-bottom:1px solid rgba(255,255,255,.5)}
.nip-head strong{font-family:"Montserrat",sans-serif;font-size:6.8px;display:block;margin-bottom:2px}
.nip table{width:100%;border-collapse:collapse}
.nip td,.nip th{border-top:1px solid rgba(255,255,255,.45);padding:2px 4px;font-weight:400;text-align:left;vertical-align:middle}
.nip th{border-left:1px solid rgba(255,255,255,.45)}
.nip td+td{border-left:1px solid rgba(255,255,255,.45)}
.ingredients{position:absolute;left:259px;top:44px;width:355px;color:var(--ink);font-size:9.6px;line-height:12.6px}
.ingredients strong{font-family:"Montserrat",sans-serif;font-size:10px;display:block;margin-bottom:2px}
.storage{position:absolute;left:424px;top:129px;width:130px;color:var(--ink);font-size:7.8px;line-height:10px;letter-spacing:.5px}
.origin-badge{position:absolute;left:424px;top:209px;width:92px;height:26px;border:2px solid var(--badge-green);border-radius:3px;background:var(--white)}
.address{position:absolute;left:524px;top:209px;width:94px;color:var(--ink);font-size:7.3px;line-height:9.5px}

/* guides */
.guide{position:absolute;background:var(--guide)}
.guide-dash-h{position:absolute;left:126px;width:648px;height:0;border-top:2px dashed var(--guide)}
.guide-dash-v{position:absolute;top:30px;height:989px;width:0;border-left:2px dashed var(--guide)}
.dim-label{position:absolute;font-size:22px;color:var(--ink);white-space:nowrap}
.dim-rot{transform:rotate(-90deg)}
.dim-flip{transform:rotate(180deg)}
.legend-swatch{position:absolute;left:253px;top:1113px;width:90px;height:59px;background:var(--window)}
.legend-text{position:absolute;left:361px;top:1126px;font-size:22px;color:var(--ink)}
</style>
</head>
<body>
<div class="sheet">

  <!-- top fold -->
  <section class="abs panel-top">
    <div class="deco deco-coconut" role="img" aria-label="Coconut slice illustration" style="left:0;top:40px;width:110px;height:110px;border-radius:50% 50% 50% 0"></div>
    <div class="deco deco-nut" role="img" aria-label="Coconut shell line illustration" style="left:20px;top:205px;width:120px;height:90px"></div>
    <div class="deco deco-apricot" role="img" aria-label="Apricot illustration" style="left:220px;top:-40px;width:142px;height:76px"></div>
    <div class="deco deco-apricot" role="img" aria-label="Apricot with leaves illustration" style="left:560px;top:22px;width:100px;height:94px;border-radius:50% 10% 50% 50%"></div>
    <div class="flipped">
      <h2 class="benefit-head">DIGESTIVE + ENERGY + IMMUNITY</h2>
      <p class="benefit-copy">Sweet, Chewy &amp; Delicious, Our Apricot &amp; Coconut Energy Ball Is Full Of Fibre For Improved Digestion; Contains Vitamin A For Maintaining Robust Immune Function And Skin Health; Potassium To Support Electrolyte Balance; Magnesium To Help With Muscle &amp; Nerve Function; And Iron For Increased Energy Levels And Cognitive Function.</p>
      <p class="join">Join Us in the Kitchen &amp; View More Healthy Recipes:</p>
      <div class="rule"></div>
      <p class="url">WWW.FERNLEAFNUTRITION.COM</p>
      <p class="social"><span>@fernleafgoodness</span><span>@fernleafnutrition</span></p>
    </div>
  </section>

  <!-- transparent window -->
  <section class="abs panel-window" role="img" aria-label="Transparent window showing the coconut-coated apricot energy ball"></section>

  <div class="title title-1">APRICOT</div>
  <div class="ampersand">&amp;</div>
  <div class="title title-2">COCONUT</div>
  <div class="title title-3">ENERGYBALL</div>

  <p class="made-local">LOCALLY<br>MADE IN<br>CANBERRA</p>
  <div class="stamp-caption">BY A NUTRITIONIST</div>

  <div class="brand-banner">
    <div class="brand-name">Fernleaf<br>Nutrition</div>
  </div>

  <div class="ing-count">6 Ingredients</div>
  <ul class="ing-list">
    <li>Dried Apricot</li>
    <li>Almond Meal</li>
    <li>Maple Syrup</li>
    <li>Coconut Oil</li>
    <li>Desiccated Coconut</li>
    <li>Vanilla Extract</li>
  </ul>

  <!-- front lower -->
  <section class="abs panel-front">
    <div class="deco deco-apricot" role="img" aria-label="Apricot with leaves illustration" style="left:0;top:18px;width:128px;height:130px"></div>
    <div class="deco deco-coconut" role="img" aria-label="Coconut slice illustration" style="left:545px;top:55px;width:110px;height:90px;border-radius:50% 0 0 50%"></div>
    <div class="deco deco-nut" role="img" aria-label="Almond line illustration" style="left:530px;top:2px;width:56px;height:38px"></div>
  </section>

  <div class="claims">
    <div class="claim">
      <svg viewBox="0 0 32 32"><circle cx="16" cy="16" r="14.5" fill="none" stroke="#fff" stroke-width="1.5"/><rect x="10" y="11" width="12" height="11" fill="none" stroke="#fff" stroke-width="1.3"/><line x1="7" y1="7" x2="25" y2="25" stroke="#fff" stroke-width="1.5"/></svg>
      <span>No Added Sugar</span>
    </div>
    <span class="claim-sep">|</span>
    <div class="claim">
      <svg viewBox="0 0 32 32"><circle cx="16" cy="16" r="14.5" fill="none" stroke="#fff" stroke-width="1.5"/><line x1="16" y1="8" x2="16" y2="25" stroke="#fff" stroke-width="1.3"/><ellipse cx="13" cy="14" rx="2.3" ry="3.5" fill="none" stroke="#fff"/><ellipse cx="19" cy="14" rx="2.3" ry="3.5" fill="none" stroke="#fff"/><line x1="7" y1="7" x2="25" y2="25" stroke="#fff" stroke-width="1.5"/></svg>
      <span>Gluten Free</span>
    </div>
    <span class="claim-sep">|</span>
    <div class="claim">
      <svg viewBox="0 0 32 32"><circle cx="16" cy="16" r="14.5" fill="none" stroke="#fff" stroke-width="1.5"/><path d="M10 22 C10 13 16 9 23 9 C23 17 18 22 10 22 Z M10 22 L18 14" fill="none" stroke="#fff" stroke-width="1.3"/></svg>
      <span>Vegan Friendly</span>
    </div>
  </div>
  <div class="benefit-pill">High Fibre --&gt; Digestive Support Healthy Fats --&gt; Sustained Energy Antioxidants --&gt; Immunity</div>
  <div class="net">40g NET</div>

  <!-- back fold (reads upside down) -->
  <section class="abs panel-back">
    <div class="deco deco-coconut" role="img" aria-label="Coconut slice illustration" style="left:0;top:48px;width:40px;height:132px;border-radius:0 50% 50% 0"></div>
    <div class="deco deco-apricot" role="img" aria-label="Apricot illustration" style="left:179px;top:232px;width:152px;height:70px"></div>
    <div class="flipped">
      <div class="nip">
        <div class="nip-head"><strong>THE GOODNESS YOU'RE RECEIVING</strong>SERVINGS PER PACKAGE: 1<br>SERVING SIZE: 40G</div>
        <table>
          <tr><td></td><th>AVERAGE QUANTITY PER SERVING</th><th>AVERAGE QUANTITY PER 100G</th></tr>
          <tr><td>ENERGY</td><td>752kJ<br>(180Cal)</td><td>1800kJ<br>(430Cal)</td></tr>
          <tr><td>PROTEIN</td><td>3.3g</td><td>8.2g</td></tr>
          <tr><td>FAT, TOTAL</td><td>13.2g</td><td>33.0g</td></tr>
          <tr><td>SATURATED</td><td>6.7g</td><td>16.7g</td></tr>
          <tr><td>CARBOHYDRATE</td><td>9.9g</td><td>24.8g</td></tr>
          <tr><td>FROM NATURAL SOURCES</td><td>9.7g</td><td>24.2g</td></tr>
          <tr><td>DIETARY FIBRE</td><td>5.6g</td><td>14g</td></tr>
          <tr><td>SODIUM</td><td>8mg</td><td>20mg</td></tr>
        </table>
      </div>
      <p class="ingredients"><strong>The Goodness You're Eating</strong>Dried Apricot (37%), Almond Meal (25%), Desiccated Coconut (25%), Maple Syrup (7%), Coconut Oil (1%), Vanilla Extract (1%). Made With love In Canberra, Australia Store In A Cool, Dry Place And Out Of Direct Sunlight</p>
      <p class="storage">ONCE OPENED, KEEP BAG TIGHTLY SEALED AND CONSUME WITHIN BEST BEFORE DATE:</p>
      <div class="origin-badge" role="img" aria-label="Country of origin badge"></div>
      <p class="address">Fernleaf Nutrition<br>14 Wattle Lane,<br>Kingston ACT 2604</p>
    </div>
  </section>

  <!-- dieline guides -->
  <div class="guide" style="left:126px;top:29px;width:649px;height:2px"></div>
  <div class="guide" style="left:126px;top:1018px;width:649px;height:2px"></div>
  <div class="guide" style="left:125px;top:29px;width:2px;height:991px"></div>
  <div class="guide" style="left:773px;top:29px;width:2px;height:991px"></div>
  <div class="guide" style="left:126px;top:292px;width:649px;height:2px"></div>
  <div class="guide" style="left:126px;top:754px;width:649px;height:2px"></div>
  <div class="guide-dash-h" style="top:60px"></div>
  <div class="guide-dash-h" style="top:986px"></div>
  <div class="guide-dash-v" style="left:743px"></div>

  <div class="guide" style="left:91px;top:30px;width:2px;height:989px"></div>
  <div class="guide" style="left:76px;top:29px;width:32px;height:2px"></div>
  <div class="guide" style="left:76px;top:60px;width:32px;height:2px"></div>
  <div class="guide" style="left:76px;top:292px;width:32px;height:2px"></div>
  <div class="guide" style="left:76px;top:754px;width:32px;height:2px"></div>
  <div class="guide" style="left:76px;top:986px;width:32px;height:2px"></div>
  <div class="guide" style="left:76px;top:1018px;width:32px;height:2px"></div>
  <span class="dim-label dim-flip" style="left:22px;top:32px">5mm</span>
  <span class="dim-label dim-rot" style="left:38px;top:164px">37.5mm</span>
  <span class="dim-label dim-rot" style="left:48px;top:494px">75mm</span>
  <span class="dim-label dim-rot" style="left:38px;top:855px">37.5mm</span>
  <span class="dim-label dim-flip" style="left:22px;top:988px">5mm</span>

  <div class="guide" style="left:126px;top:1046px;width:649px;height:2px"></div>
  <div class="guide" style="left:125px;top:1032px;width:2px;height:30px"></div>
  <div class="guide" style="left:773px;top:1032px;width:2px;height:30px"></div>
  <span class="dim-label" style="left:452px;top:1060px">105mm</span>

  <div class="legend-swatch"></div>
  <span class="legend-text">Transparent Window</span>
</div>
</body>
</html>
```